Vacation Rental Postcard Design

The Kingfisher's Perch is a vacation rental cottage. We want a postcard that can be used as promotional give-aways for visitors as well as something that can be given to the tourism board and local merchants to help us promote the rental.

Our tag line is" The Kingfisher's Perch - the finest perch on the ridge!". Should also include "Snohomish, WA USA"

We have also used "Come see what all of the buzz is about"

Want to include our info in small print on the mailing side portion of the postcard:

KLWT: www.klwtstays.example/417294
Chatterly: www.chatterly.example/thefinestperchontheridge

Target Market(s)

Couples, romantic, honeymooners, coming for wine tasting, hot air ballooning, hiking, enjoying nature

Industry/Entity Type

Tourism

```html
<!DOCTYPE html>
<html lang="en">
<head>
<meta charset="utf-8">
<title>The Kingfisher's Perch – Postcard</title>
<link href="https://fonts.googleapis.com/css2?family=Yesteryear&family=Oswald:wght@500;600&family=Signika:wght@500;600;700&display=swap" rel="stylesheet">
<style>
  :root {
    --backdrop: #efeae0;
    --teal: #1d9aa1;
    --sand: #ddd3b4;
    --ink: #2b2118;
    --cream: #efe6c8;
    --orange: #e8792b;
    --listing: #2b6f8f;
    --paper: #ffffff;
    --rule: #9a9a9a;
  }
  * { box-sizing: border-box; margin: 0; padding: 0; }
  html, body { width: 1200px; height: 500px; overflow: hidden; }
  body { background: var(--backdrop); position: relative; font-family: "Signika", sans-serif; }

  .card { position: absolute; top: 30px; width: 561px; height: 434px; overflow: hidden; }
  .card--front { left: 25px; background: var(--teal); }
  .card--back { left: 612px; background: var(--paper); }

  .photo { position: absolute; }

  /* front */
  .front-brand { position: absolute; left: 10px; top: 12px; width: 145px; height: 86px;
    display: flex; align-items: center; gap: 8px; }
  .front-brand .dot { width: 14px; height: 14px; border-radius: 50%; background: var(--ink); flex: none; }
  .front-brand .name { font-family: "Yesteryear", cursive; font-size: 21px; line-height: 1.05; color: var(--ink); }
  .front-location { position: absolute; left: 12px; top: 106px; width: 143px; text-align: center;
    font-weight: 600; font-size: 12px; letter-spacing: 0.3px; color: var(--cream); white-space: nowrap; }

  .front-header { position: absolute; left: 163px; top: 0; width: 398px; height: 103px; background: var(--sand); }
  .front-header .title { position: absolute; left: 12px; top: 10px; font-family: "Yesteryear", cursive;
    font-size: 44px; line-height: 1.1; color: var(--ink); white-space: nowrap; }
  .front-header .tagline { position: absolute; left: 15px; top: 62px; font-family: "Oswald", sans-serif;
    font-weight: 600; font-size: 23px; letter-spacing: 1.2px; color: var(--ink); text-transform: uppercase; white-space: nowrap; }

  .photo--hero { left: 167px; top: 105px; width: 391px; height: 208px;
    background: linear-gradient(180deg, #6f7780 0%, #8c9496 30%, #3d5a2e 55%, #5d7a3c 80%, #7d8f4a 100%); }
  .hero-line { position: absolute; left: 183px; top: 256px; font-family: "Signika", sans-serif; font-weight: 500;
    font-size: 27px; line-height: 27px; color: var(--cream); }

  .photo--house { left: 12px; top: 133px; width: 143px; height: 180px;
    background: linear-gradient(180deg, #cfe1f0 0%, #6f9a5a 35%, #2f4f3b 60%, #a59c8a 100%); }
  .photo--living { left: 12px; top: 323px; width: 130px; height: 96px; background: linear-gradient(180deg, #caa061, #7a4a24); }
  .photo--bedroom { left: 150px; top: 323px; width: 130px; height: 96px; background: linear-gradient(180deg, #d8b46a, #e9e6d8); }
  .photo--dining { left: 288px; top: 323px; width: 130px; height: 96px; background: linear-gradient(180deg, #d9c7a0, #6a4a2c); }
  .photo--exterior { left: 427px; top: 323px; width: 119px; height: 96px; background: linear-gradient(180deg, #7fb3e0, #3b3026 60%, #6a8a4a); }
  .leaves { position: absolute; left: 430px; top: 4px; width: 131px; height: 150px;
    background: radial-gradient(ellipse at 60% 40%, rgba(128,184,60,0.75), rgba(128,184,60,0) 70%); }

  /* back */
  .back-message { position: absolute; left: 0; top: 0; width: 298px; height: 434px; background: var(--sand); }
  .back-message .title { position: absolute; left: 0; width: 298px; top: 14px; text-align: center;
    font-family: "Yesteryear", cursive; font-size: 30px; line-height: 1.1; color: var(--ink); white-space: nowrap; }
  .back-message .tagline { position: absolute; left: 0; width: 298px; top: 54px; text-align: center;
    font-family: "Oswald", sans-serif; font-weight: 600; font-size: 18px; letter-spacing: 0.6px;
    color: var(--ink); text-transform: uppercase; white-space: nowrap; }
  .blurb { position: absolute; left: 20px; top: 90px; width: 270px; font-weight: 600; font-size: 13px;
    line-height: 18px; color: var(--ink); }
  .blurb span { display: block; white-space: nowrap; }
  .blurb .indent-1 { padding-left: 14px; }
  .blurb .indent-2 { padding-left: 23px; }
  .photo--sunset { left: 50px; top: 180px; width: 203px; height: 150px;
    background: linear-gradient(180deg, #d36a8a 0%, #e47b66 45%, #3a2630 75%, #1c1418 100%); }

  .listings { position: absolute; left: 0; width: 298px; top: 348px; display: flex; justify-content: center;
    align-items: center; gap: 14px; }
  .listing { display: flex; align-items: center; gap: 6px; font-weight: 600; font-size: 20px; color: var(--listing); }
  .listing .square { width: 22px; height: 22px; background: var(--listing); }
  .contact { position: absolute; left: 0; width: 298px; top: 380px; text-align: center; font-weight: 700;
    font-size: 11.5px; line-height: 16px; color: var(--orange); white-space: nowrap; }
  .back-location { position: absolute; left: 0; width: 298px; top: 413px; text-align: center; font-weight: 600;
    font-size: 11.5px; letter-spacing: 0.3px; color: var(--ink); white-space: nowrap; }

  .back-brand { position: absolute; left: 324px; top: 40px; width: 120px; display: flex; align-items: center; gap: 7px; }
  .back-brand .dot { width: 12px; height: 12px; border-radius: 50%; background: var(--ink); flex: none; }
  .back-brand .name { font-family: "Yesteryear", cursive; font-size: 19px; line-height: 1.05; color: var(--ink); }
  .stamp-box { position: absolute; left: 454px; top: 19px; width: 88px; height: 88px; border: 1px solid var(--rule); }
  .address-lines { position: absolute; left: 328px; top: 212px; width: 215px; }
  .address-lines span { display: block; height: 1px; background: var(--rule); margin-bottom: 35px; }
</style>
</head>
<body>
  <section class="card card--front">
    <div class="front-brand">
      <span class="dot"></span>
      <span class="name">The Kingfisher's Perch</span>
    </div>
    <p class="front-location">Snohomish, WA USA</p>
    <header class="front-header">
      <h1 class="title">The Kingfisher's Perch</h1>
      <p class="tagline">The Finest Perch On The Ridge!</p>
    </header>
    <div class="photo photo--hero" role="img" aria-label="Photo of the cottage grounds with evergreens, lawn and a rainbow under a stormy sky"></div>
    <p class="hero-line">Come see what all<br>of the buzz is about</p>
    <div class="leaves" role="img" aria-label="Illustration of green leaves on a branch"></div>
    <div class="photo photo--house" role="img" aria-label="Photo of the green cottage exterior with front steps"></div>
    <div class="photo photo--living" role="img" aria-label="Photo of the living room with wood floors"></div>
    <div class="photo photo--bedroom" role="img" aria-label="Photo of the bedroom with a white quilted bed"></div>
    <div class="photo photo--dining" role="img" aria-label="Photo of the dining area with flowers on the table"></div>
    <div class="photo photo--exterior" role="img" aria-label="Photo of the dark cottage exterior under blue sky"></div>
  </section>

  <section class="card card--back">
    <div class="back-message">
      <h2 class="title">The Kingfisher's Perch</h2>
      <p class="tagline">The Finest Perch On The Ridge</p>
      <p class="blurb">
        <span class="indent-2">Private view cottage on 2 country acres,</span>
        <span class="indent-1">Romantic, refreshing.relaxing, reconnect</span>
        <span>1 bedroom, 1.5 bath apartment, spectacular</span>
        <span>mountain, valley and river view.</span>
      </p>
      <div class="photo photo--sunset" role="img" aria-label="Photo of a pink sunset over silhouetted evergreen trees"></div>
      <div class="listings">
        <span class="listing"><span class="square"></span>Chatterly</span>
        <span class="listing">KLWT</span>
      </div>
      <p class="contact">KLWT: www.klwtstays.example/417294<br>www.chatterly.example/thefinestperchontheridge</p>
      <p class="back-location">Snohomish, WA USA</p>
    </div>
    <div class="back-brand">
      <span class="dot"></span>
      <span class="name">The Kingfisher's Perch</span>
    </div>
    <div class="stamp-box"></div>
    <div class="address-lines"><span></span><span></span><span></span><span></span></div>
  </section>
</body>
</html>
```